Business card for law firm

Need business card for new law firm. Think confident, authoritative, conservative, but not stuffy or old-fashioned.

Contact Information for Business Card

Content for card - logo (uploaded), plus the following:

Paul Whitcombe (larger font)
Managing Partner (larger font, but not as large as name)
Level 9, 7 Ferris Lane
Sydney NSW 2000
Main Tel 02 9364 2710
Direct Tel 02 8472 3159
Email paul@qvlegal.com.au
www.qvlegal.com.au

Letterhead design should include logo plus:
Level 9, 7 Ferris Lane
Sydney NSW 2000
Tel 02 8472 3159
www.qvlegal.com.au

```html
<!DOCTYPE html>
<html lang="en">
<head>
<meta charset="utf-8">
<title>Quayvale Legal – Business Card</title>
<link rel="stylesheet" href="https://fonts.googleapis.com/css2?family=Cinzel:wght@500;600&family=Montserrat:wght@400;500&display=swap">
<style>
  :root {
    --backdrop: #1c1c1e;
    --card-navy: #232a6b;
    --card-navy-deep: #1d235c;
    --ink-white: #ffffff;
    --ink-soft: #e6e8f4;
  }
  * { margin: 0; padding: 0; box-sizing: border-box; }
  html, body {
    width: 1200px; height: 900px; overflow: hidden;
    background: var(--backdrop);
  }
  .canvas {
    position: relative; width: 1200px; height: 900px;
    display: flex; flex-direction: column; align-items: center;
    justify-content: center; gap: 30px;
  }
  .card {
    width: 700px; height: 400px;
    background: var(--card-navy);
    position: relative;
    box-shadow: 0 14px 30px rgba(0,0,0,0.5);
  }
  .card-back .pattern-field {
    position: absolute; inset: 0;
    background: linear-gradient(120deg, var(--card-navy-deep) 0%, var(--card-navy) 55%, #3a428a 100%);
  }
  .card-front {
    display: flex; align-items: center;
  }
  .brand {
    width: 360px; display: flex; flex-direction: column; align-items: center;
    color: var(--ink-white);
    font-family: "Cinzel", serif; font-weight: 600;
  }
  .brand-square {
    width: 54px; height: 54px; background: var(--ink-white); margin-bottom: 22px;
  }
  .brand-name { font-size: 44px; letter-spacing: 2px; line-height: 1; }
  .brand-sub { font-size: 15px; letter-spacing: 16px; margin-top: 8px; padding-left: 16px; }
  .divider {
    width: 1.5px; height: 230px; background: var(--ink-white);
  }
  .contact {
    padding-left: 34px; color: var(--ink-white);
    font-family: "Montserrat", sans-serif; font-weight: 400;
  }
  .person-name {
    font-family: "Cinzel", serif; font-weight: 600; font-size: 25px; line-height: 1.1;
  }
  .person-role { font-size: 16px; color: var(--ink-soft); margin-bottom: 14px; }
  .address { font-size: 17px; line-height: 1.3; margin-bottom: 12px; }
  .contact-list { list-style: none; font-size: 17px; line-height: 1.55; }
  .contact-list li { display: flex; align-items: center; gap: 12px; }
  .contact-list svg { width: 15px; height: 15px; flex: none; }
</style>
</head>
<body>
<main class="canvas">
  <section class="card card-back">
    <div class="pattern-field" role="img" aria-label="Embossed repeating brand pattern on navy card back"></div>
  </section>

  <section class="card card-front">
    <div class="brand">
      <div class="brand-square"></div>
      <div class="brand-name">QUAYVALE</div>
      <div class="brand-sub">LEGAL</div>
    </div>
    <div class="divider"></div>
    <div class="contact">
      <h1 class="person-name">PAUL WHITCOMBE</h1>
      <p class="person-role">Managing Partner</p>
      <p class="address">Level 9, 7 Ferris Lane<br>Sydney NSW 2000</p>
      <ul class="contact-list">
        <li>
          <svg viewBox="0 0 16 16" fill="none" stroke="#fff" stroke-width="1.4"><path d="M4 1.5 L6 4.5 L4.8 6 C5.6 8 8 10.4 10 11.2 L11.5 10 L14.5 12 L13 14.5 C7 14 2 9 1.5 3 Z"/></svg>
          02 9364 2710
        </li>
        <li>
          <svg viewBox="0 0 16 16" fill="none" stroke="#fff" stroke-width="1.4"><rect x="4" y="1" width="8" height="14" rx="1.5"/><line x1="7" y1="12.5" x2="9" y2="12.5"/></svg>
          02 8472 3159
        </li>
        <li>
          <svg viewBox="0 0 16 16" fill="none" stroke="#fff" stroke-width="1.4"><rect x="1" y="3.5" width="14" height="9" rx="1"/><path d="M1.5 4 L8 9 L14.5 4"/></svg>
          paul@qvlegal.com.au
        </li>
        <li>
          <svg viewBox="0 0 16 16" fill="none" stroke="#fff" stroke-width="1.3"><circle cx="8" cy="8" r="6.5"/><ellipse cx="8" cy="8" rx="2.8" ry="6.5"/><line x1="1.5" y1="8" x2="14.5" y2="8"/></svg>
          www.qvlegal.com.au
        </li>
      </ul>
    </div>
  </section>
</main>
</body>
</html>
```